We are a recruitment company based in Norwich/Cambridge England.
I have included our company logo which we want to remain the same.

What we are looking for is a new creative Business card which will really stand out!!

Contact Information for Business Card

Harriet Dunmore
email: Harriet@plavex.co.uk
Address: Brackwell House
Fenmoor Enterprise Park
Partridge Way
Norwich
QB9 3KX
Tel:01632 960418

```html
<!DOCTYPE html>
<html lang="en">
<head>
<meta charset="utf-8">
<title>Plavex Business Card</title>
<link rel="stylesheet" href="https://fonts.googleapis.com/css2?family=Roboto:wght@400;500;700&display=swap">
<style>
  :root {
    --green: #7dbb3a;
    --green-dark: #6aa62c;
    --green-tint: #8cc443;
    --grey: #878387;
    --ink: #2b2b2b;
    --paper: #ffffff;
    --paper-shade: #ececec;
    --backdrop: #e4e6e3;
    --mark-light: #d9d9d9;
  }
  * { box-sizing: border-box; margin: 0; padding: 0; }
  html, body { width: 1200px; height: 900px; overflow: hidden; }
  body {
    background: var(--backdrop);
    font-family: "Roboto", Arial, sans-serif;
    display: flex;
    align-items: center;
    justify-content: center;
    gap: 40px;
  }
  .card {
    position: relative;
    width: 540px;
    height: 309px;
    border-radius: 16px;
    overflow: hidden;
    box-shadow: 0 10px 30px rgba(0,0,0,0.18);
  }
  /* Front */
  .card-front {
    background: linear-gradient(160deg, var(--paper) 45%, var(--paper-shade) 100%);
  }
  .brand {
    position: absolute;
    left: 32px;
    top: 30px;
  }
  .brand-row { display: flex; align-items: center; gap: 10px; }
  .brand-dot {
    width: 34px; height: 34px; border-radius: 50%;
    background: var(--green);
  }
  .brand-name {
    font-size: 38px; font-weight: 700; color: var(--green);
    line-height: 1; letter-spacing: -0.5px;
  }
  .brand-tagline {
    margin: 4px 0 0 46px;
    font-size: 8px; letter-spacing: 2.6px; color: var(--grey);
  }
  .contact {
    position: absolute;
    left: 32px;
    top: 130px;
    width: 250px;
    list-style: none;
    font-size: 13px;
    line-height: 19px;
    color: var(--ink);
  }
  .contact-item { display: flex; align-items: center; gap: 8px; }
  .contact-item svg { width: 11px; height: 11px; flex: none; }
  .contact-address { margin-top: 6px; }
  .web-accent { color: var(--green); }
  .person {
    position: absolute;
    right: 32px;
    top: 130px;
    text-align: right;
  }
  .person-name { font-size: 21px; font-weight: 500; color: var(--green); letter-spacing: 0.5px; }
  .person-role { font-size: 13px; color: var(--ink); letter-spacing: 1px; margin-top: 2px; }
  .front-mark {
    position: absolute;
    left: 310px;
    top: 182px;
    width: 112px;
    height: 112px;
    border-radius: 50%;
    background: var(--green);
  }
  /* Back */
  .card-back {
    background: linear-gradient(135deg, var(--green-tint) 0%, var(--green-dark) 100%);
  }
  .back-glow {
    position: absolute;
    right: -60px; top: -40px;
    width: 360px; height: 360px; border-radius: 50%;
    background: rgba(255,255,255,0.06);
  }
  .back-brand {
    position: absolute;
    left: 0; right: 0; top: 96px;
    text-align: center;
  }
  .back-brand .brand-row { justify-content: center; gap: 14px; }
  .back-brand .brand-dot { width: 46px; height: 46px; background: var(--mark-light); }
  .back-brand .brand-name { font-size: 56px; color: var(--mark-light); }
  .back-brand .brand-tagline {
    margin: 8px 0 0 60px; font-size: 10px; letter-spacing: 3.4px; color: #e8e8e8;
  }
  .back-web {
    position: absolute;
    left: 0; right: 0; bottom: 40px;
    text-align: center;
    font-size: 14px; letter-spacing: 1.5px; color: #f0f0f0;
  }
</style>
</head>
<body>
  <section class="card card-front">
    <div class="brand">
      <div class="brand-row">
        <span class="brand-dot"></span>
        <span class="brand-name">Plavex</span>
      </div>
      <p class="brand-tagline">Technology Recruitment</p>
    </div>

    <ul class="contact">
      <li class="contact-item">
        <svg viewBox="0 0 12 12" aria-hidden="true"><path d="M3 1 L5 3.5 L4 5 Q5 7 7 8 L8.5 7 L11 9 L10 11 Q4 11 1 2 Z" fill="var(--green)"/></svg>
        <span>01632 960418</span>
      </li>
      <li class="contact-item">
        <svg viewBox="0 0 12 12" aria-hidden="true"><rect x="1" y="2.5" width="10" height="7" fill="none" stroke="var(--green)" stroke-width="1.3"/><path d="M1 3 L6 7 L11 3" fill="none" stroke="var(--green)" stroke-width="1.3"/></svg>
        <span>Harriet@plavex.co.uk</span>
      </li>
      <li class="contact-item">
        <svg viewBox="0 0 12 12" aria-hidden="true"><circle cx="6" cy="6" r="5" fill="none" stroke="var(--green)" stroke-width="1.2"/><ellipse cx="6" cy="6" rx="2.2" ry="5" fill="none" stroke="var(--green)" stroke-width="1"/><path d="M1 6 H11" stroke="var(--green)" stroke-width="1"/></svg>
        <span>www.<span class="web-accent">plavex</span>.co.uk</span>
      </li>
      <li class="contact-address">Brackwell House, Fenmoor Enterprise Park</li>
      <li>Partridge Way, Norwich QB9 3KX</li>
    </ul>

    <div class="person">
      <p class="person-name">Harriet Dunmore</p>
      <p class="person-role">Founder</p>
    </div>

    <div class="front-mark" role="img" aria-label="Company symbol area"></div>
  </section>

  <section class="card card-back">
    <div class="back-glow"></div>
    <div class="back-brand">
      <div class="brand-row">
        <span class="brand-dot"></span>
        <span class="brand-name">Plavex</span>
      </div>
      <p class="brand-tagline">Technology Recruitment</p>
    </div>
    <p class="back-web">www.plavex.co.uk</p>
  </section>
</body>
</html>
```